Bloom Path! A website showcasing who I am as a person

Bloom Path started out as idea for me to better myself as a person and work on small projects that would help me grow as a person. Now I want to build a website showcasing "Bloom Path." I want the website to showcase who I am and how I have grown both professionally and personally. I can build the raw code of the website on my own but I am not really much of a designer. I am looking for a design where I can write and post blogs, articles and share my thoughts. A little about myself and the ideas and interests that I want to share
What is Bloom Path
Who I am
Background - Professional
Brand Marketing
Email Automation
Hiking
Rock Climbing
Traveling
Exercising and Transformation
"Personal Thoughts"
Hopefully this is enough information to get people started on some designs.
Work
3 page

```html
<!DOCTYPE html>
<html lang="en">
<head>
<meta charset="utf-8">
<title>Mira Dalton — Bloom Path</title>
<link rel="stylesheet" href="https://fonts.googleapis.com/css2?family=Roboto+Condensed:wght@400;700&family=Open+Sans:ital,wght@0,400;0,600;1,400&display=swap">
<style>
:root{
  --blue:#3577c4;
  --blue-light:#4d8fd8;
  --blue-dark:#2a64a8;
  --ink:#333;
  --text:#666;
  --muted:#888;
  --line:#e6e6e6;
  --card:#f9f9f9;
  --teal:#6cbcbc;
  --star:#f0a81c;
  --footer:#232323;
}
*{box-sizing:border-box;margin:0;padding:0}
html,body{width:1200px;height:2571px;overflow:hidden;background:#fff}
body{position:relative;font-family:"Open Sans",sans-serif;color:var(--text)}
.abs{position:absolute}

/* header */
.logo{left:98px;top:40px;font-family:"Roboto Condensed",sans-serif;font-weight:700;font-size:35px;letter-spacing:1px;color:var(--ink)}
.logo span{color:var(--blue)}
.tagline{left:549px;top:50px;font-family:"Roboto Condensed",sans-serif;font-size:14px;color:#444}
.search{left:869px;top:41px;width:231px;height:35px;border:1px solid #ddd;border-radius:3px;font-size:11px;color:#555;padding:10px 10px;font-family:"Roboto Condensed",sans-serif}
.search svg{position:absolute;right:12px;top:11px}

/* nav */
.nav{left:0;top:122px;width:1200px;height:51px;background:linear-gradient(var(--blue-light),var(--blue-dark));display:flex;padding-left:82px}
.nav a{font-family:"Roboto Condensed",sans-serif;font-size:12.5px;color:#fff;text-decoration:none;padding:0 16px;line-height:51px;border-right:1px solid rgba(255,255,255,.2)}
.nav a:last-child{border:none}

/* hero */
.hero{left:0;top:173px;width:1200px;height:547px;background:linear-gradient(100deg,#cfd9e3 0%,#9fb2c6 35%,#3e5570 62%,#22344c 100%)}
.hero-title{left:98px;top:318px;font-family:"Roboto Condensed",sans-serif;font-weight:700;font-size:40px;color:#fff}
.hero-copy{left:98px;top:376px;width:360px;font-size:12px;line-height:20px;color:#fff}
.btn{left:98px;top:454px;width:116px;height:35px;background:var(--blue);border-radius:3px;color:#fff;font-family:"Roboto Condensed",sans-serif;font-size:12.5px;line-height:35px;text-align:center}
.dots{left:100px;top:511px;display:flex;gap:8px;align-items:center}
.dots i{width:10px;height:10px;border-radius:50%;background:#fff;display:block}
.dots i.on{width:16px;height:16px;background:none;border:2px solid #fff;position:relative}
.dots i.on::after{content:"";position:absolute;left:3px;top:3px;width:6px;height:6px;border-radius:50%;background:#fff}
.wave{left:0;top:640px}

/* posts */
.post{left:98px;width:691px;height:255px;background:var(--card);border:1px solid var(--line);display:flex}
.post-img{width:305px;height:100%;flex:none}
.post-body{padding:22px 30px 0 30px}
.post-title{font-size:16.5px;line-height:24px;color:#444}
.meta{margin-top:18px;padding:10px 0;border-top:1px solid var(--line);font-size:11px;font-style:italic;color:#777;display:flex;gap:26px}
.meta span::before{content:"";display:inline-block;width:8px;height:8px;background:#888;margin-right:7px;border-radius:2px}
.excerpt{font-size:11.5px;line-height:20.5px;color:#666}
.share{margin-top:10px;display:flex;align-items:center;gap:10px;font-weight:600;font-size:14px;color:var(--blue)}
.share i{width:11px;height:11px;border-radius:50%;background:#444;display:block}

.pages{left:98px;top:2248px;display:flex;gap:9px;align-items:center;font-size:11px}
.pages b{width:26px;height:26px;border:1px solid #999;text-align:center;line-height:24px;font-weight:400;color:#444}
.pages b.on,.pages b.next{background:var(--teal);border-color:var(--teal);color:#fff}

/* sidebar */
.who{left:836px;top:800px;width:264px;height:302px;background:var(--card);border:1px solid var(--line);text-align:center}
.who-top{height:83px;background:var(--blue)}
.avatar{position:absolute;left:75px;top:21px;width:114px;height:114px;border-radius:50%;border:4px solid #fff;background:linear-gradient(#c9b6aa,#5a4a44)}
.who h3{margin-top:72px;font-family:"Roboto Condensed",sans-serif;font-weight:400;font-size:15px;color:#444;letter-spacing:.5px}
.who p{margin:8px 22px 0;font-size:11px;line-height:20.5px;font-style:italic;color:#555}
.stars{color:var(--star);font-size:11px;letter-spacing:1px}
.stars s{color:#ccc;text-decoration:none}
.who .stars{margin-top:10px}

.side-title{left:836px;top:1128px;font-family:"Roboto Condensed",sans-serif;font-size:21px;color:#444}
.review{left:836px;width:264px;height:140px;border-bottom:1px solid var(--line);display:flex;gap:16px}
.review-img{width:100px;height:106px;flex:none}
.review h4{font-weight:400;font-size:13px;color:#444;margin-top:0}
.review .stars{margin:5px 0 4px}
.review p{font-size:11px;line-height:18px;color:#555}
.review .by{margin-top:12px;font-size:11px;color:#555}

.gallery{left:836px;top:1642px;width:264px;height:304px;background:var(--card);border:1px solid var(--line);text-align:center}
.gallery-head{height:38px;background:#1f1f1f;color:#fff;font-family:"Roboto Condensed",sans-serif;font-weight:700;font-size:16px;line-height:38px;position:relative}
.gallery-head svg{position:absolute;top:13px}
.gallery-img{height:183px;background:linear-gradient(120deg,#6f8a55,#a9b9a2 45%,#d84a56 75%,#7a9a5c)}
.gallery p{margin-top:14px;font-size:11px;line-height:20px;font-style:italic;color:#555}
.promo{left:836px;top:1975px;width:264px;height:257px;border:2px solid #d6c07a;background:linear-gradient(160deg,#d8e3e8,#9fb4c2 60%,#c9534a)}

/* footer */
.footer{left:0;top:2366px;width:1200px;height:205px;background:var(--footer);text-align:center;color:#fff}
.social{display:flex;justify-content:center;gap:10px;margin-top:60px}
.social i{width:24px;height:24px;border-radius:4px;background:#fff;display:block}
.links{margin-top:12px;font-size:13px}
.links span{margin:0 8px}
.copy{margin-top:8px;font-size:13px}
</style>
</head>
<body>

<header>
  <div class="abs logo">MIRA <span>DALTON</span></div>
  <div class="abs tagline">Exercising and Transformation &nbsp;|&nbsp; "Personal Thoughts"</div>
  <div class="abs search">SEARCH
    <svg width="12" height="12" viewBox="0 0 12 12"><circle cx="5" cy="5" r="3.8" fill="none" stroke="#333" stroke-width="1.6"/><path d="M8 8l3 3" stroke="#333" stroke-width="1.8"/></svg>
  </div>
</header>

<nav class="abs nav">
  <a>WHAT IS BLOOM PATH</a><a>WHO I AM</a><a>BACKGROUND - PROFESSIONAL</a><a>BRAND MARKETING</a><a>EMAIL AUTOMATION</a><a>HIKING</a><a>ROCK CLIMBING</a><a>TRAVELING</a>
</nav>

<section>
  <div class="abs hero" role="img" aria-label="Photo of two colleagues in suits reviewing work at a desk"></div>
  <h1 class="abs hero-title">BLOOM PATH.</h1>
  <p class="abs hero-copy">Sed ut perspiciatis unde omnis iste natus error sit voluptatem accusantium doloremque laudantium, totam rem aperiam, eaque ipsa quae ab illo inventore veritatis.</p>
  <div class="abs btn">READ MORE &#9656;</div>
  <div class="abs dots"><i class="on"></i><i></i><i></i><i></i></div>
  <svg class="abs wave" width="1200" height="90" viewBox="0 0 1200 90" preserveAspectRatio="none">
    <path d="M0 50 C250 0 500 10 700 35 C900 60 1050 55 1200 20 L1200 90 L0 90Z" fill="#fff"/>
    <path d="M0 52 C250 2 500 12 700 37 C900 62 1050 57 1200 22" fill="none" stroke="#2f6db5" stroke-width="5"/>
    <path d="M0 62 C260 15 520 28 720 50 C900 70 1060 64 1200 36" fill="none" stroke="#5b9ade" stroke-width="2"/>
  </svg>
</section>

<main>
  <article class="abs post" style="top:794px">
    <div class="post-img" style="background:linear-gradient(135deg,#c7b49c,#7b8fa6)" role="img" aria-label="Photo of a woman sitting on an office desk"></div>
    <div class="post-body">
      <h2 class="post-title" style="font-weight:400">Nemo enim ipsam voluptatem quia voluptas sit aspernatur aut odit aut fugit</h2>
      <div class="meta"><span>March 25, 2017</span><span>2 comments</span><span>by David</span></div>
      <p class="excerpt">Lorem ipsum dolor sit amet, consectetur adipiscing elit, sed do eiusmod tempor incididunt ut labore et dolore magna aliqua. Ut enim ad minim veniam, quis nostrud exercitation labo-ris nisi ut aliquip ex ea commodo</p>
      <div class="share">Share : <i></i><i></i><i></i></div>
    </div>
  </article>
  <article class="abs post" style="top:1077px">
    <div class="post-img" style="background:linear-gradient(135deg,#dfe6ee,#35404e)" role="img" aria-label="Photo of two businessmen in conversation"></div>
    <div class="post-body">
      <h2 class="post-title" style="font-weight:400">Nemo enim ipsam voluptatem quia voluptas sit aspernatur aut odit aut fugit</h2>
      <div class="meta"><span>March 25, 2017</span><span>2 comments</span><span>by David</span></div>
      <p class="excerpt">Lorem ipsum dolor sit amet, consectetur adipiscing elit, sed do eiusmod tempor incididunt ut labore et dolore magna aliqua. Ut enim ad minim veniam, quis nostrud exercitation labo-ris nisi ut aliquip ex ea commodo</p>
      <div class="share">Share : <i></i><i></i><i></i></div>
    </div>
  </article>
  <article class="abs post" style="top:1360px">
    <div class="post-img" style="background:linear-gradient(135deg,#8fb2cc,#e2e6e8)" role="img" aria-label="Photo of colleagues meeting around a table"></div>
    <div class="post-body">
      <h2 class="post-title" style="font-weight:400">Nemo enim ipsam voluptatem quia voluptas sit aspernatur aut odit aut fugit</h2>
      <div class="meta"><span>March 25, 2017</span><span>2 comments</span><span>by David</span></div>
      <p class="excerpt">Lorem ipsum dolor sit amet, consectetur adipiscing elit, sed do eiusmod tempor incididunt ut labore et dolore magna aliqua. Ut enim ad minim veniam, quis nostrud exercitation labo-ris nisi ut aliquip ex ea commodo</p>
      <div class="share">Share : <i></i><i></i><i></i></div>
    </div>
  </article>
  <article class="abs post" style="top:1643px">
    <div class="post-img" style="background:linear-gradient(160deg,#b4ccdb,#6e93b0)" role="img" aria-label="Illustration of a woman holding a bunch of sketched balloons"></div>
    <div class="post-body">
      <h2 class="post-title" style="font-weight:400">Nemo enim ipsam voluptatem quia voluptas sit aspernatur aut odit aut fugit</h2>
      <div class="meta"><span>March 25, 2017</span><span>2 comments</span><span>by David</span></div>
      <p class="excerpt">Lorem ipsum dolor sit amet, consectetur adipiscing elit, sed do eiusmod tempor incididunt ut labore et dolore magna aliqua. Ut enim ad minim veniam, quis nostrud exercitation labo-ris nisi ut aliquip ex ea commodo</p>
      <div class="share">Share : <i></i><i></i><i></i></div>
    </div>
  </article>
  <article class="abs post" style="top:1926px">
    <div class="post-img" style="background:linear-gradient(160deg,#e4e7ea,#a9b1b8 70%,#6d747b)" role="img" aria-label="Photo of a hand with a magnifying glass over a city and a globe"></div>
    <div class="post-body">
      <h2 class="post-title" style="font-weight:400">Nemo enim ipsam voluptatem quia voluptas sit aspernatur aut odit aut fugit</h2>
      <div class="meta"><span>March 25, 2017</span><span>2 comments</span><span>by David</span></div>
      <p class="excerpt">Lorem ipsum dolor sit amet, consectetur adipiscing elit, sed do eiusmod tempor incididunt ut labore et dolore magna aliqua. Ut enim ad minim veniam, quis nostrud exercitation labo-ris nisi ut aliquip ex ea commodo</p>
      <div class="share">Share : <i></i><i></i><i></i></div>
    </div>
  </article>

  <div class="abs pages"><b class="on">1</b><b>2</b><b>3</b><span>.......</span><b>10</b><b class="next">&raquo;</b></div>
</main>

<aside>
  <div class="abs who">
    <div class="who-top"></div>
    <div class="avatar" role="img" aria-label="Portrait photo of the author"></div>
    <h3>WHO I AM</h3>
    <p>Lorem ipsum dolor sit amet, consectetur adipiscing elit, sed do eiusmod tempor incididunt ut labore et dolore magna aliqua. Ut enim ad minim veniam, quis nostrud &nbsp;Lorem</p>
    <div class="stars">★★★<s>★★</s></div>
  </div>

  <h3 class="abs side-title" style="font-weight:400">REVIEWS</h3>
  <div class="abs review" style="top:1178px">
    <div class="review-img" style="background:linear-gradient(135deg,#9bb46a,#4f6a3a)" role="img" aria-label="Photo of a cyclist on a forest trail"></div>
    <div><h4>Nemo enim ipsam</h4><div class="stars">★★★<s>★★</s></div><p>Lorem ipsum dolor sit amet, consectetur adipiscing elit,</p><div class="by">&#9679; Medlems</div></div>
  </div>
  <div class="abs review" style="top:1332px">
    <div class="review-img" style="background:linear-gradient(135deg,#8a9aa8,#4d5a48)" role="img" aria-label="Photo of hikers on a mountain path"></div>
    <div><h4>Nemo enim ipsam</h4><div class="stars">★★★<s>★★</s></div><p>Lorem ipsum dolor sit amet, consectetur adipiscing elit,</p><div class="by">&#9679; Medlems</div></div>
  </div>
  <div class="abs review" style="top:1486px">
    <div class="review-img" style="background:linear-gradient(135deg,#c2ccd4,#3c5070)" role="img" aria-label="Photo of an older hiker outdoors"></div>
    <div><h4>Nemo enim ipsam</h4><div class="stars">★★★<s>★★</s></div><p>Lorem ipsum dolor sit amet, consectetur adipiscing elit,</p><div class="by">&#9679; Medlems</div></div>
  </div>

  <div class="abs gallery">
    <div class="gallery-head">
      <svg style="left:14px" width="8" height="12" viewBox="0 0 8 12"><path d="M7 1L2 6l5 5" fill="none" stroke="#fff" stroke-width="2"/></svg>
      SNAPSHOTS
      <svg style="right:14px" width="8" height="12" viewBox="0 0 8 12"><path d="M1 1l5 5-5 5" fill="none" stroke="#fff" stroke-width="2"/></svg>
    </div>
    <div class="gallery-img" role="img" aria-label="Photo of a joyful traveller by a waterfall"></div>
    <p>Lorem ipsum dolor sit amet, consectetur<br>adipiscing elit, sed do eiusmod</p>
    <div class="stars">★★★<s>★★</s></div>
  </div>

  <div class="abs promo" role="img" aria-label="Advert photo of a runner with a running shoe"></div>
</aside>

<footer class="abs footer">
  <div class="social"><i></i><i></i><i></i><i></i><i></i></div>
  <div class="links">Home<span>/</span>Contact<span>/</span>Topics<span>/</span>About Mira Dalton<span>/</span>Discussion<span>/</span>Videos Links</div>
  <div class="copy">Copyright @ 2017 Mira Dalton. All Rights Reserved.</div>
</footer>

</body>
</html>
```